Need Business Card ASAP

We need a business card design for a meeting coming up in a few days. The company name is Harlow Ridge Building and Construction and the logo is attached. Something clean, cool, and contemporary that we can get to a printer right away. Attached is the business card for Volmar Energy, an affiliated company, which we like. Instead of the hawk on the back, you could use the attached "D". We'll also be needing matching letterhead in the near future, so ideas for that are welcome.

```html
<!DOCTYPE html>
<html lang="en">
<head>
<meta charset="utf-8">
<title>Harlow Ridge Building and Construction – Business Card</title>
<link rel="stylesheet" href="https://fonts.googleapis.com/css2?family=Source+Sans+3:wght@400;600;700&display=swap">
<style>
  :root {
    --backdrop: #7a5a3c;
    --card-white: #ffffff;
    --band-grey: #dedede;
    --ink-dark: #3f3f3f;
    --ink-body: #333333;
    --gold-light: #e4e0c9;
    --gold-mid: #cfc89f;
    --gold-deep: #b9b07c;
    --mark-white: #ffffff;
  }
  * { margin: 0; padding: 0; box-sizing: border-box; }
  html, body {
    width: 1034px;
    height: 1200px;
    overflow: hidden;
  }
  body {
    background: var(--backdrop);
    font-family: "Source Sans 3", Arial, sans-serif;
    position: relative;
  }
  .card {
    position: absolute;
    left: 70px;
    width: 887px;
    height: 507px;
    box-shadow: 0 2px 6px rgba(0,0,0,0.35);
  }
  /* Front */
  .card-front {
    top: 71px;
    background: var(--card-white);
  }
  .name-band {
    height: 73px;
    background: var(--band-grey);
    display: flex;
    align-items: center;
    justify-content: center;
    color: var(--ink-dark);
    font-weight: 700;
    font-size: 32px;
    letter-spacing: 0.3px;
  }
  .name-band .title {
    font-size: 22px;
    margin-left: 6px;
    margin-top: 6px;
  }
  .brand {
    position: absolute;
    top: 98px;
    left: 0;
    right: 0;
    display: flex;
    flex-direction: column;
    align-items: center;
  }
  .brand-square {
    width: 150px;
    height: 150px;
    background: linear-gradient(135deg, var(--gold-deep), var(--gold-light));
  }
  .brand-name {
    margin-top: 16px;
    font-size: 30px;
    font-weight: 600;
    color: var(--ink-dark);
  }
  .contact-row {
    position: absolute;
    left: 0;
    right: 0;
    display: flex;
    justify-content: center;
    gap: 28px;
    color: var(--ink-body);
    font-size: 23px;
  }
  .contact-row.phones { top: 338px; }
  .contact-row.online { top: 383px; }
  .contact-item { display: flex; align-items: center; gap: 6px; }
  .contact-item svg { width: 20px; height: 20px; fill: var(--ink-body); }
  .company-band {
    position: absolute;
    left: 0; right: 0; bottom: 0;
    height: 73px;
    background: var(--band-grey);
    text-align: center;
    color: var(--ink-dark);
  }
  .company-name {
    font-size: 29px;
    font-weight: 700;
    line-height: 1;
    padding-top: 8px;
  }
  .company-address {
    font-size: 22px;
    margin-top: 4px;
  }
  /* Back */
  .card-back {
    top: 617px;
    background: radial-gradient(ellipse at 55% 45%, var(--gold-light) 0%, var(--gold-mid) 70%, var(--gold-deep) 120%);
    display: flex;
    align-items: center;
    justify-content: center;
  }
  .back-name {
    color: var(--mark-white);
    font-size: 64px;
    font-weight: 700;
  }
</style>
</head>
<body>

<section class="card card-front">
  <header class="name-band">YOUR NAME,<span class="title">TITLE</span></header>

  <div class="brand">
    <div class="brand-square"></div>
    <div class="brand-name">Harlow Ridge</div>
  </div>

  <div class="contact-row phones">
    <span class="contact-item">
      <svg viewBox="0 0 24 24" aria-hidden="true"><path d="M6.6 10.8a15 15 0 0 0 6.6 6.6l2.2-2.2c.3-.3.7-.4 1-.2 1.1.4 2.3.6 3.6.6.6 0 1 .4 1 1V20c0 .6-.4 1-1 1A17 17 0 0 1 3 4c0-.6.4-1 1-1h3.5c.6 0 1 .4 1 1 0 1.3.2 2.5.6 3.6.1.3 0 .7-.2 1z"/></svg>
      (123) 456-7890
    </span>
    <span class="contact-item">
      <svg viewBox="0 0 24 24" aria-hidden="true"><path d="M8 1h8a2 2 0 0 1 2 2v18a2 2 0 0 1-2 2H8a2 2 0 0 1-2-2V3a2 2 0 0 1 2-2zm0 3v13h8V4zm4 15a1 1 0 1 0 0 2 1 1 0 0 0 0-2z"/></svg>
      (123) 456-7890
    </span>
  </div>

  <div class="contact-row online">
    <span class="contact-item">
      <svg viewBox="0 0 24 24" aria-hidden="true"><path d="M2 5h20v14H2zm2 2v.5l8 5 8-5V7zm0 2.8V17h16V9.8l-8 5z"/></svg>
      yourname@harlowridgebuild.com
    </span>
    <span class="contact-item">
      <svg viewBox="0 0 24 24" aria-hidden="true"><path d="M12 2a10 10 0 1 0 0 20 10 10 0 0 0 0-20zm6.9 9h-3a15 15 0 0 0-1.3-5.6A8 8 0 0 1 18.9 11zM12 4c.9 1.2 1.8 3.6 1.9 7h-3.8C10.2 7.6 11.1 5.2 12 4zM9.4 5.4A15 15 0 0 0 8.1 11h-3a8 8 0 0 1 4.3-5.6zM5.1 13h3a15 15 0 0 0 1.3 5.6A8 8 0 0 1 5.1 13zM12 20c-.9-1.2-1.8-3.6-1.9-7h3.8c-.1 3.4-1 5.8-1.9 7zm2.6-1.4a15 15 0 0 0 1.3-5.6h3a8 8 0 0 1-4.3 5.6z"/></svg>
      www.harlowridgebuild.com
    </span>
  </div>

  <footer class="company-band">
    <div class="company-name">Harlow Ridge Building &amp; Construction</div>
    <div class="company-address">00, Complex Name, Street, City 00000</div>
  </footer>
</section>

<section class="card card-back">
  <div class="back-name">Harlow Ridge</div>
</section>

</body>
</html>
```